Tall ridge firewood

It a new firewood outlet in Jindabyne nsw that will only sell top hardwood firewood (ironbark , red gum, grey gum, an box mix. I would like to see a web page the we can do order online payment for delivery. It will all so need to have photos of the firewood. I all so have logo for tall ridge firewood
Must have a modem look but easy to use I would like to see a black back ground of some sort.

Here are some other firewood web pages for ideas and firewood info
http://www.example-logpile.com.au
http://www.example-stackwood.com.au
http://www.example-splitlog.com.au
http://www.example-kendaltimber.com.au/firewood

Industry/Entity Type

Firewood

```html
<!DOCTYPE html>
<html lang="en">
<head>
<meta charset="utf-8">
<title>Tall Ridge Firewood</title>
<link rel="stylesheet" href="https://fonts.googleapis.com/css2?family=Oswald:wght@400;500&family=Yanone+Kaffeesatz:wght@400;600;700&family=Open+Sans:wght@400;600;700&display=swap">
<style>
:root{
  --black:#0d0d0d;
  --white:#ffffff;
  --blue:#1f7ac8;
  --blue-light:#2e8fd9;
  --blue-dark:#14579a;
  --orange:#f36c1a;
  --grey-text:#7a7a7a;
  --panel:#1c1c1c;
  --card:#252525;
  --body-text:#cfcfcf;
  --muted:#9a9a9a;
  --wood-1:#c79a62;
  --wood-2:#8a5e34;
  --wood-3:#4a3220;
}
*{margin:0;padding:0;box-sizing:border-box}
html,body{width:1024px;height:1200px;overflow:hidden}
body{position:relative;background:var(--panel);font-family:"Open Sans",sans-serif;color:var(--body-text)}
.abs{position:absolute}

.header{left:0;top:0;width:1024px;height:146px;background:var(--white);border-top:4px solid var(--black)}
.email-tab{left:600px;top:0;width:288px;height:27px;background:var(--black);border-radius:0 0 14px 14px;color:var(--white);font-size:10px;text-align:center;line-height:24px}
.brand{left:137px;top:10px;width:172px;height:128px;text-align:center}
.brand-mark{width:92px;height:92px;border-radius:50%;border:3px solid var(--black);margin:0 auto 4px;background:#f2f2f2}
.brand-name{font-family:"Oswald",sans-serif;font-weight:500;font-size:16px;color:var(--blue-dark);text-transform:uppercase;letter-spacing:.3px;white-space:nowrap}
.call{left:485px;top:46px;font-family:"Oswald",sans-serif;font-size:21px;color:var(--grey-text);display:flex;align-items:center;gap:7px;white-space:nowrap}
.call b{font-weight:400;color:var(--blue)}
.order-btn{left:776px;top:43px;width:112px;height:36px;background:linear-gradient(#ff8a3a,var(--orange));border:1px solid #d9570f;border-radius:3px;color:var(--white);font-family:"Oswald",sans-serif;font-size:15px;text-align:center;line-height:34px}
.cards{left:589px;top:91px;display:flex;gap:11px}
.cards span{width:40px;height:25px;border-radius:2px;border:1px solid #ddd}

.nav{left:0;top:146px;width:1024px;height:41px;background:linear-gradient(#3a9ae0,var(--blue-dark));border-top:1px solid #6db7ec}
.nav a{position:absolute;top:10px;font-family:"Oswald",sans-serif;font-size:15px;color:#eaf4fc;text-decoration:none;text-shadow:0 1px 1px rgba(0,0,0,.4)}

.hero{left:0;top:187px;width:1024px;height:413px;background:radial-gradient(ellipse at 40% 35%,var(--wood-1),var(--wood-2) 55%,var(--wood-3))}
.hero-title{left:138px;top:462px;font-family:"Yanone Kaffeesatz",sans-serif;font-weight:600;font-size:30px;line-height:34px;color:var(--white);text-shadow:0 1px 3px rgba(0,0,0,.6)}
.hero-band{left:0;top:544px;width:1024px;height:56px;background:rgba(30,30,30,.72)}
.hero-cta{left:138px;top:551px;font-family:"Yanone Kaffeesatz",sans-serif;font-weight:600;font-size:32px;color:var(--white)}
.hero-cta em{font-style:normal;color:var(--blue-light)}

.h2{font-family:"Yanone Kaffeesatz",sans-serif;font-weight:600;font-size:23px;color:var(--white);text-transform:uppercase;line-height:24px}
.h2 em{font-style:normal;color:var(--blue)}
.about-title{left:137px;top:636px}
.about-photo{left:137px;top:670px;width:176px;height:153px;background:linear-gradient(#4a4a4a,#2a1208 30%,#a3320e 55%,#2a1a12 80%,#3d3d3d)}
.about-text{left:329px;top:668px;width:305px;font-size:10px;line-height:16px}
.about-text p+p{margin-top:16px}
.guarantee{left:134px;top:876px}
.guarantee-text{left:135px;top:930px;width:250px;font-size:10px;line-height:16px}
.checklist{left:390px;top:878px;list-style:none}
.checklist li{display:flex;align-items:center;gap:10px;height:27px;font-size:12px;font-weight:600;color:#d8d8d8}
.checklist i{width:15px;height:15px;border-radius:50%;background:#555;display:flex;align-items:center;justify-content:center}

.promo{left:647px;width:240px;height:109px;background:var(--card);box-shadow:0 1px 4px rgba(0,0,0,.5)}
.promo-photo{position:absolute;left:0;top:0;width:84px;height:109px;background:linear-gradient(#e8e4df,#b9aea4)}
.promo-body{position:absolute;left:94px;top:20px}
.promo-title{font-family:"Yanone Kaffeesatz",sans-serif;font-weight:600;font-size:21px;color:var(--white);line-height:20px}
.promo-sub{font-family:"Yanone Kaffeesatz",sans-serif;font-weight:600;font-size:15px;color:var(--white);line-height:18px}
.promo-note{font-family:"Yanone Kaffeesatz",sans-serif;font-size:11.5px;color:var(--muted);margin-top:8px;letter-spacing:.3px;line-height:12px}
.promo-phone{font-family:"Yanone Kaffeesatz",sans-serif;font-weight:600;font-size:23px;color:var(--white);line-height:24px}

.footer{left:0;top:1018px;width:1024px;height:145px;background:linear-gradient(#4e4e4e,#2f2f2f);border-top:1px solid #666}
.footer-brand{left:160px;top:1030px;width:160px;text-align:center}
.footer-brand .brand-mark{width:90px;height:90px;margin-bottom:2px;background:transparent;border-color:#1a1a1a}
.footer-brand .brand-name{color:#2a4256;font-size:14px;line-height:18px}
.footer-col{top:1041px;width:140px}
.footer-col h4{font-size:12px;font-weight:700;color:var(--white);line-height:17px;margin-bottom:8px}
.footer-col ul{list-style:none}
.footer-col li{font-size:8.5px;color:#b8b8b8;height:19px;display:flex;align-items:center;gap:8px;letter-spacing:.2px;white-space:nowrap}
.footer-col li.tall{height:24px}
.footer-map{left:647px;top:1046px;width:241px;height:102px;background:linear-gradient(135deg,#e9e5dc,#dcd7cc)}

.bottom{left:0;top:1163px;width:1024px;height:37px;background:#1f1f1f}
.copyright{left:137px;top:1175px;font-size:8.5px;color:#9a9a9a}
.legal{left:688px;top:1177px;font-size:8.5px;color:#9a9a9a;display:flex;gap:10px}
.social{top:1171px;width:21px;height:21px;border-radius:2px;background:var(--blue-dark)}
</style>
</head>
<body>

<header class="abs header"></header>
<div class="abs email-tab">email us: info@tallridgefirewood.com.au</div>

<div class="abs brand">
  <div class="brand-mark"></div>
  <div class="brand-name">Tall Ridge Firewood</div>
</div>

<div class="abs call">
  <svg width="18" height="18" viewBox="0 0 18 18"><rect width="18" height="18" rx="3" fill="#1f7ac8"/><path d="M5 4c1 0 1.5 2 1.5 2.5S5.5 7.5 5.8 8.3c.5 1.3 2.4 3.3 3.9 3.9.8.3 1.3-.7 1.8-.7s2.5.5 2.5 1.5-1 1.5-2 1.5C8 14.5 3.5 10 3.5 6 3.5 5 4 4 5 4z" fill="#fff"/></svg>
  <span>CALL US TODAY <b>+1800.555.0142</b></span>
</div>
<div class="abs order-btn">ORDER ONLINE</div>

<div class="abs cards">
  <span style="background:#f4f4f4"></span>
  <span style="background:#fbe6b8"></span>
  <span style="background:#f4f4f4"></span>
  <span style="background:#1c3d8c;border-color:#1c3d8c"></span>
  <span style="background:#1a2f6e;border-color:#1a2f6e"></span>
  <span style="background:#2a7fc6;border-color:#2a7fc6"></span>
</div>

<nav class="abs nav">
  <a style="left:136px">HOME</a>
  <a style="left:213px">ABOUT US</a>
  <a style="left:316px">OUR PRODUCTS</a>
  <a style="left:452px">FAQ</a>
  <a style="left:518px">DELIVERY</a>
  <a style="left:614px">CONTACT</a>
</nav>

<section class="abs hero" role="img" aria-label="Photo of a pile of cut hardwood logs"></section>
<h1 class="abs hero-title">Are you looking for the BEST<br>LONG LASTING firewood money can buy?</h1>
<div class="abs hero-band"></div>
<p class="abs hero-cta">Call us today for <em>FREE</em> quote: <em>1(800) 555-0142</em></p>

<h2 class="abs h2 about-title">About <em>Tall Ridge Firewood</em></h2>
<div class="abs about-photo" role="img" aria-label="Photo of a wood fire burning in a fireplace"></div>
<div class="abs about-text">
  <p>It is a long established fact that a reader will be distracted by the readable content of a page when looking at its layout. The point of using Lorem Ipsum is that it has a more-or-less normal distribution of letters, as opposed to using 'Content here, content here', making it look like readable English.</p>
  <p>Lorem ipsum dolor sit amet, consectetur adipisicing elit, sed do eiusmod tempor incididunt ut labore et dolore magna aliqua. Ut enim ad minim veniam, quis nostrud exercitation ullamco laboris nisi ut aliquip ex ea commodo consequat.</p>
</div>

<h2 class="abs h2 guarantee">Our Guarantee:<br><em>Long Lasting Quality</em></h2>
<p class="abs guarantee-text">Lorem ipsum dolor sit amet, consectetur adipisicing elit, sed do eiusmod tempor incididunt ut labore et dolore magna aliqua.</p>
<ul class="abs checklist">
  <li><i><svg width="6" height="8" viewBox="0 0 6 8"><path d="M1 1l3 3-3 3" stroke="#fff" stroke-width="1.5" fill="none"/></svg></i>Best quality firewood</li>
  <li><i><svg width="6" height="8" viewBox="0 0 6 8"><path d="M1 1l3 3-3 3" stroke="#fff" stroke-width="1.5" fill="none"/></svg></i>Long-lasting</li>
  <li><i><svg width="6" height="8" viewBox="0 0 6 8"><path d="M1 1l3 3-3 3" stroke="#fff" stroke-width="1.5" fill="none"/></svg></i>Fast &amp; reliable service</li>
  <li><i><svg width="6" height="8" viewBox="0 0 6 8"><path d="M1 1l3 3-3 3" stroke="#fff" stroke-width="1.5" fill="none"/></svg></i>We guarantee 100% satisfaction</li>
</ul>

<div class="abs promo" style="top:622px">
  <div class="promo-photo" role="img" aria-label="Photo of a delivery worker holding parcels and a clipboard"></div>
  <div class="promo-body">
    <div class="promo-title">WE DELIVER</div>
    <div class="promo-sub">for your convenience</div>
    <div class="promo-note">CALL US OR ORDER LINE</div>
  </div>
</div>
<div class="abs promo" style="top:751px">
  <div class="promo-photo" role="img" aria-label="Photo of a customer using a tablet"></div>
  <div class="promo-body">
    <div class="promo-title">ORDER ONLINE</div>
    <div class="promo-sub">for easy transactions</div>
    <div class="promo-note">GUARANTEED QUALITY SERVICE</div>
  </div>
</div>
<div class="abs promo" style="top:881px">
  <div class="promo-photo" role="img" aria-label="Photo of a support agent wearing a headset"></div>
  <div class="promo-body" style="top:18px">
    <div class="promo-sub">Questions? Call us:</div>
    <div class="promo-phone">(800)555-0142</div>
    <div class="promo-note">CONTACT US AND WE'LL BE<br>GLAD TO ASSIST YOU.</div>
  </div>
</div>

<footer class="abs footer"></footer>
<div class="abs footer-brand">
  <div class="brand-mark"></div>
  <div class="brand-name">Tall Ridge Firewood</div>
</div>

<div class="abs footer-col" style="left:377px">
  <h4>Navigation</h4>
  <ul>
    <li><svg width="4" height="6"><path d="M0 0l4 3-4 3z" fill="#888"/></svg>Home</li>
    <li><svg width="4" height="6"><path d="M0 0l4 3-4 3z" fill="#888"/></svg>About</li>
    <li><svg width="4" height="6"><path d="M0 0l4 3-4 3z" fill="#888"/></svg>Services</li>
    <li><svg width="4" height="6"><path d="M0 0l4 3-4 3z" fill="#888"/></svg>Contact</li>
  </ul>
</div>
<div class="abs footer-col" style="left:504px">
  <h4>Contact Us</h4>
  <ul>
    <li class="tall"><svg width="10" height="10" viewBox="0 0 10 10"><path d="M2 0c1 0 1.5 2 1.5 2.5S2.6 3.4 3 4c.6 1.2 1.8 2.4 3 3 .6.3 1-.5 1.5-.5S10 7 10 8s-1 2-2 2C4 10 0 6 0 2 0 1 1 0 2 0z" fill="#999"/></svg>+1800-555-0142</li>
    <li class="tall"><svg width="11" height="8" viewBox="0 0 11 8"><rect width="11" height="8" fill="#999"/><path d="M0 0l5.5 4.5L11 0" stroke="#3a3a3a" fill="none"/></svg>orders@tallridge.com.au</li>
    <li class="tall"><svg width="8" height="11" viewBox="0 0 8 11"><path d="M4 0a4 4 0 0 1 4 4c0 3-4 7-4 7S0 7 0 4a4 4 0 0 1 4-4z" fill="#999"/><circle cx="4" cy="4" r="1.5" fill="#3a3a3a"/></svg>Your Address, Your Country</li>
    <li style="padding-left:16px">Your Zip Code</li>
  </ul>
</div>
<div class="abs footer-map" role="img" aria-label="Street map showing the store location"></div>

<div class="abs bottom"></div>
<p class="abs copyright">Copyright 2014 © Tall Ridge Firewood - All Rights Reserved</p>
<div class="abs legal"><span>Site Map</span><span>•</span><span>Privacy Policy</span></div>
<span class="abs social" style="left:809px"></span>
<span class="abs social" style="left:838px"></span>
<span class="abs social" style="left:866px"></span>

</body>
</html>
```